Website for Briar Hollow Gathering Church

Wordpress website design required for Briar Hollow Gathering Church. We are a family oriented church catering for age groups from school age to elderly people. The church has a wide variety of activities which it coordinates. The idea is to describe the activities on the activities page, but cross-link them to show which would be applicable to the different age groups.

We would like an inviting website which is easy to read and navigate.

Target Market(s)

Very wide audience - from school age youth to elderly people, so design and style should cater for both audiences.

Industry/Entity Type

Church

Coding

Coded - Design and coding required

Number of Pages Required

5+ page

Font styles to use
Sans Serif

Colors
0255a3
ffffff
0792cd
f78f20

Requirements
Must have
• Inviting website.
• Clear readable font.
• Space to import photos to balance text on each page.
• Need to project a dynamic and progressive feel for the church.
• Easy to navigate.
Nice to have
• Scrolling photos on pages. Ability to enter questions/ comments/prayer requests on Home page.
Should not have
• Conservative audience, so should not be too bold.

```html
<!DOCTYPE html>
<html lang="en">
<head>
<meta charset="utf-8">
<title>Briar Hollow Gathering Church</title>
<link href="https://fonts.googleapis.com/css2?family=Merriweather:ital,wght@0,300;0,400;0,700;1,300;1,400&family=Open+Sans:wght@400;600&display=swap" rel="stylesheet">
<style>
:root{
  --blue-deep:#0255a3;
  --blue-bright:#0792cd;
  --orange:#f78f20;
  --white:#ffffff;
  --grey-bg:#f6f6f6;
  --card-bg:#f4f4f4;
  --text-muted:#9a9a9a;
  --footer-top:#3c434a;
  --footer-bottom:#22262b;
  --serif:'Merriweather', Georgia, serif;
}
*{margin:0;padding:0;box-sizing:border-box}
html,body{width:1200px;height:2951px;overflow:hidden}
body{position:relative;background:var(--white);font-family:var(--serif);color:#555}
.abs{position:absolute}
.center{left:0;width:1200px;text-align:center}

/* header */
.site-header{top:0;left:0;width:1200px;height:142px;background:radial-gradient(ellipse at 50% 0%,#ffffff 0%,#f3f3f3 100%)}
.brand{top:74px;left:0;width:1200px;display:flex;justify-content:center;align-items:center;gap:10px}
.brand-dot{width:12px;height:12px;border-radius:50%;background:var(--blue-deep)}
.brand-name{font-family:var(--serif);font-size:19px;font-weight:400;color:var(--blue-deep)}

.main-nav{top:142px;left:0;width:1200px;height:74px;background:linear-gradient(#0a63b6,var(--blue-deep))}
.nav-link{top:22px;font-size:20px;color:var(--white);font-weight:300}
.nav-link.active::after{content:"";position:absolute;left:0;right:0;bottom:-10px;height:3px;background:var(--orange)}

/* hero */
.hero{top:216px;left:0;width:1200px;height:606px;background:linear-gradient(180deg,#6b4f34 0%,#8a6a4a 22%,#a9a7a2 45%,#5e5a52 70%,#3b3a3a 100%)}
.hero-title{top:508px;font-size:32px;font-weight:300;color:var(--white)}
.hero-sub{top:562px;font-size:16px;font-weight:300;color:rgba(255,255,255,.55)}
.btn{display:flex;align-items:center;justify-content:center;background:linear-gradient(#fb9a2f,#f0800f);color:var(--white);font-family:var(--serif);font-weight:300;border-radius:2px}
.hero-btn{top:630px;left:533px;width:134px;height:41px;font-size:13px}
.hero-dots{left:1146px;top:552px;display:flex;flex-direction:column;gap:12px}
.hero-dots span{width:9px;height:9px;border-radius:50%;background:var(--white)}
.hero-dots span.on{background:var(--orange)}

/* welcome */
.welcome{top:822px;left:0;width:1200px;height:392px;background:var(--grey-bg)}
.section-title{font-size:29px;font-weight:400;color:var(--blue-deep)}
.welcome-title{top:893px}
.welcome-text{top:964px;left:200px;width:800px;text-align:center;font-size:15px;line-height:29px;color:var(--text-muted);font-weight:300}
.welcome-btn{top:1117px;left:533px;width:134px;height:42px;font-size:13px}

/* activity */
.activity-title{top:1262px}
.arrow{top:1270px}
.card{top:1336px;width:256px;height:267px;background:var(--card-bg)}
.card-photo{position:absolute;left:12px;top:12px;width:232px;height:167px}
.card-text{position:absolute;left:18px;right:18px;top:206px;text-align:center;font-size:12px;line-height:19px;color:var(--text-muted);font-weight:300}

/* news */
.news-title{top:1683px;left:202px;font-size:29px;color:var(--blue-bright);font-weight:400}
.news-rule{top:1731px;left:202px;width:529px;height:1px;background:#e2e2e2}
.news-item{top:1757px;width:255px}
.news-photo{width:255px;height:169px}
.news-date{margin-top:14px;font-size:10.5px;font-style:italic;color:var(--blue-deep)}
.news-text{margin-top:11px;font-size:17px;line-height:22px;color:var(--text-muted);font-weight:300}

.minister{top:1672px;left:747px;width:254px;height:378px;background:linear-gradient(#0a98d4,#0a6fbf);overflow:hidden}
.minister-logo{position:absolute;left:16px;top:20px;width:222px;height:118px;background:var(--white);display:flex;align-items:center;justify-content:center;gap:6px}
.minister-logo .brand-dot{width:8px;height:8px}
.minister-logo .brand-name{font-size:12px}
.minister-heading{position:absolute;left:16px;right:16px;top:154px;font-size:25px;line-height:36px;color:var(--white);font-weight:400;white-space:nowrap}
.minister-text{position:absolute;left:16px;right:16px;top:238px;font-size:12.5px;line-height:18px;font-style:italic;color:var(--white);font-weight:300}
.minister-btn{position:absolute;left:16px;top:321px;width:140px;height:37px;font-size:13px}

/* prayer */
.prayer{top:2120px;left:0;width:1200px;height:461px;background:linear-gradient(180deg,#7a5a3a 0%,#9b7454 30%,#7a6a55 60%,#4f5a4d 100%)}
.prayer-title{top:2224px;font-size:30px;font-weight:300;color:var(--white)}
.prayer-text{top:2301px;left:200px;width:800px;text-align:center;font-size:16px;line-height:29px;color:var(--white);font-weight:300}
.prayer-form{top:2382px;left:269px;width:661px;height:69px;border:1px solid rgba(255,255,255,.7)}
.prayer-input{position:absolute;left:26px;top:26px;font-size:11.5px;color:var(--white);font-weight:300}
.prayer-btn{position:absolute;left:482px;top:9px;width:164px;height:48px;font-size:16px;text-transform:uppercase}

/* footer */
.site-footer{top:2581px;left:0;width:1200px;height:370px;background:linear-gradient(var(--footer-top),var(--footer-bottom))}
.footer-col{top:2621px}
.footer-heading{font-size:13.5px;color:var(--orange);font-weight:300;margin-bottom:25px}
.footer-list{list-style:none;font-size:11px;line-height:28.5px;color:var(--white)}
.footer-address{font-size:11px;line-height:21px;color:var(--white)}
.social{display:flex;align-items:center;gap:14px;font-size:11px;color:var(--white)}
.social i{width:7px;height:7px;border-radius:50%;background:var(--orange)}
.copyright{top:2914px;font-size:10.5px;color:var(--white)}
</style>
</head>
<body>

<header class="abs site-header">
  <div class="abs brand"><span class="brand-dot"></span><span class="brand-name">Briar Hollow Gathering Church</span></div>
</header>

<nav class="abs main-nav">
  <span class="abs nav-link active" style="left:224px">Home</span>
  <span class="abs nav-link" style="left:325px">Age Group</span>
  <span class="abs nav-link" style="left:468px">Activities</span>
  <span class="abs nav-link" style="left:602px">Events Calendar</span>
  <span class="abs nav-link" style="left:799px">About</span>
  <span class="abs nav-link" style="left:901px">Contact</span>
</nav>

<section class="abs hero" role="img" aria-label="Church interior with wooden vaulted ceiling, cross and rows of pews"></section>
<h1 class="abs center hero-title">Briar Hollow Gathering Church</h1>
<p class="abs center hero-sub">At vero eos et accusamus et iusto odio dignissimos ducimust qui blanditiis</p>
<a class="abs btn hero-btn">Learn More</a>
<div class="abs hero-dots"><span class="on"></span><span></span><span></span><span></span></div>

<section class="abs welcome"></section>
<h2 class="abs center section-title welcome-title">Welcome To Briar Hollow Gathering Church</h2>
<p class="abs welcome-text">At vero eos et accusamus et iusto odio dignissimos ducimust qui blanditiis praesentium voluptatum deleniti atque corrupti quos dolores et quas molestias excepturi sint occaecati cupiditate non provident, similique sunt in culpa qui officia deserunt mollitia animi, id est laborum et dolorum fuga. Et harum quidem rerum facilis est et expedita distinctio.</p>
<a class="abs btn welcome-btn">Learn More</a>

<h2 class="abs center section-title activity-title">Activity</h2>
<svg class="abs arrow" style="left:201px" width="12" height="20" viewBox="0 0 12 20"><path d="M9 3 L3 10 L9 17" fill="none" stroke="#0255a3" stroke-width="2.5"/></svg>
<svg class="abs arrow" style="left:966px" width="12" height="20" viewBox="0 0 12 20"><path d="M3 3 L9 10 L3 17" fill="none" stroke="#0255a3" stroke-width="2.5"/></svg>

<article class="abs card" style="left:201px">
  <div class="card-photo" role="img" aria-label="Cathedral nave with arches and pews" style="background:linear-gradient(#6a4a2c,#a87a45 50%,#4a3524)"></div>
  <p class="card-text">At vero eos et accusamus et iusto odio dignissimos ducimust qui</p>
</article>
<article class="abs card" style="left:476px">
  <div class="card-photo" role="img" aria-label="Person praying quietly in a church" style="background:linear-gradient(90deg,#8a7a6c,#c9b8a4 50%,#7c6a5c)"></div>
  <p class="card-text">At vero eos et accusamus et iusto odio dignissimos ducimust qui</p>
</article>
<article class="abs card" style="left:747px">
  <div class="card-photo" role="img" aria-label="Wooden cross draped with red cloth against a cloudy sky" style="background:linear-gradient(135deg,#5d7270,#9fb0a4 50%,#6e7e72)"></div>
  <p class="card-text">At vero eos et accusamus et iusto odio dignissimos ducimust qui</p>
</article>

<h2 class="abs news-title">News</h2>
<div class="abs news-rule"></div>
<article class="abs news-item" style="left:201px">
  <div class="news-photo" role="img" aria-label="Small chapel on a hill at dusk" style="background:linear-gradient(#4e3f46,#a06a4a 55%,#2f2a26)"></div>
  <p class="news-date">Posted On 22nd October 2016</p>
  <p class="news-text">At vero eos et accusamus et iusto odio dignissimos ducimust qui</p>
</article>
<article class="abs news-item" style="left:476px">
  <div class="news-photo" role="img" aria-label="Stone church tower among green trees under blue sky" style="background:linear-gradient(#7fb4e6,#c8a86a 55%,#6f8a3c)"></div>
  <p class="news-date">Posted On 22nd October 2016</p>
  <p class="news-text">At vero eos et accusamus et iusto odio dignissimos ducimust qui</p>
</article>

<aside class="abs minister">
  <div class="minister-logo"><span class="brand-dot"></span><span class="brand-name">Briar Hollow Gathering Church</span></div>
  <h3 class="minister-heading">Minister’s<br>Weekly Message</h3>
  <p class="minister-text">At vero eos et accusamus et iusto odio dignissimos ducimus qui blanditiis praesentium</p>
  <a class="btn minister-btn">Read Messages</a>
</aside>

<section class="abs prayer" role="img" aria-label="Aerial view of a town with a church spire at sunset"></section>
<h2 class="abs center prayer-title">Prayer Request</h2>
<p class="abs prayer-text">At vero eos et accusamus et iusto odio dignissimos ducimust qui blanditiis praesentium voluptatum deleniti atque corrupti quos dolores et quas molestias excepturi</p>
<div class="abs prayer-form">
  <span class="prayer-input">Enter Your E-mail Address</span>
  <a class="btn prayer-btn">Send Request</a>
</div>

<footer class="abs site-footer"></footer>
<div class="abs footer-col" style="left:201px">
  <h4 class="footer-heading">Quick Links</h4>
  <ul class="footer-list"><li>Home</li><li>Age Group</li><li>Activities</li><li>Events Calendar</li><li>About</li><li>Contact</li></ul>
</div>
<div class="abs footer-col" style="left:405px">
  <h4 class="footer-heading">Other Links</h4>
  <ul class="footer-list"><li>Privacy Policy</li><li>Terms Of Service</li></ul>
</div>
<div class="abs footer-col" style="left:629px;top:2629px">
  <h4 class="footer-heading">Address</h4>
  <p class="footer-address">Linden 14 Str. 40210, Norvale<br>Eastbrook, Westland<br>+44-2105550147 (landline)<br>+44-6975550283 (mobile phone)</p>
</div>
<div class="abs footer-col" style="left:865px">
  <h4 class="footer-heading">Connect With Us</h4>
  <div class="social"><i></i><span>Community Feed</span></div>
</div>
<p class="abs center copyright">© 2016 Company Name &nbsp;|&nbsp; All Rights Reserved</p>

</body>
</html>
```